VelkaVision.com

Complete Website Design (Godaddy) and company Branding / Logo Design. The products will sell are only done in-person and are installed. So this site does not need to be an e-commerce site. We will only be giving out information and collecting customer inquires. Website will only need to be about 3 to 5 pages.

```html
<!DOCTYPE html>
<html lang="en">
<head>
<meta charset="utf-8">
<title>Velka Vision — Professional TV Installation Services</title>
<link href="https://fonts.googleapis.com/css2?family=Playfair+Display:wght@900&family=Mulish:wght@400;600;700&display=swap" rel="stylesheet">
<style>
:root{
  --ink:#111111;
  --text:#222222;
  --accent:#45b6ec;
  --white:#ffffff;
  --panel:#e3e4e5;
  --wave-shade:#e4e0df;
  --footer:#060606;
}
*{box-sizing:border-box;margin:0;padding:0}
html,body{width:772px;height:1200px;overflow:hidden;background:var(--white)}
body{position:relative;font-family:"Mulish",sans-serif;color:var(--text)}
.serif{font-family:"Playfair Display",serif;font-weight:900;color:var(--ink)}

.hero{position:absolute;left:0;top:0;width:772px;height:460px;overflow:hidden;
  background:linear-gradient(90deg,#f6f6f6 0%,#f2f1f0 35%,#e7e2dc 55%,#cfc7bf 75%,#e9e6e3 100%)}
.hero-photo{position:absolute;left:290px;top:0;width:482px;height:430px;
  background:radial-gradient(ellipse at 55% 45%,#2c2c30 0%,#5a4c44 28%,rgba(200,190,180,.6) 60%,rgba(240,238,236,0) 85%)}
.hero-fade{position:absolute;left:0;top:0;width:420px;height:460px;
  background:linear-gradient(90deg,rgba(248,248,248,1) 55%,rgba(248,248,248,0))}
.logo{position:absolute;left:85px;top:22px;font-size:21px;letter-spacing:.2px}
.phone{position:absolute;left:464px;top:21px;width:129px;height:25px;border:1px solid var(--ink);
  border-radius:13px;display:flex;align-items:center;font-size:9.5px;color:var(--ink)}
.phone-icon{width:25px;height:25px;border:1px solid var(--ink);border-radius:50%;margin-left:-1px;
  display:flex;align-items:center;justify-content:center;background:var(--white)}
.phone span{margin-left:12px}
.btn{position:absolute;background:var(--accent);color:var(--white);border-radius:30px;
  display:flex;align-items:center;justify-content:center;font-weight:600}
.btn-contact{left:607px;top:21px;width:82px;height:26px;font-size:9.5px}
.hero h1{position:absolute;left:83px;top:146px;font-size:36px;line-height:44px}
.hero-sub{position:absolute;left:83px;top:291px;font-size:12.5px;color:var(--ink)}
.btn-quote{left:83px;top:331px;width:142px;height:35px;font-size:12px;font-weight:700}
.wave{position:absolute;left:0;width:772px}

.welcome{position:absolute;left:120px;top:516px;width:534px;height:160px;border:1px solid var(--ink);border-radius:16px}
.welcome h2{position:absolute;left:0;right:0;top:-18px;text-align:center;font-size:22px}
.welcome h2 span{background:var(--white);padding:0 20px}
.rule{position:absolute;height:2px;width:26px;background:var(--accent)}
.welcome .rule{left:253px;top:34px}
.welcome p{position:absolute;left:50px;right:50px;top:62px;text-align:center;font-size:9px;line-height:14.4px;color:var(--text)}

.quote{position:absolute;left:0;top:722px;width:772px;height:360px;background:var(--panel)}
.quote-photo{position:absolute;left:0;top:0;width:335px;height:340px;
  background:radial-gradient(ellipse at 58% 62%,#fbfbfb 0%,#f1f1f1 35%,rgba(227,228,229,0) 70%)}
.quote h2{position:absolute;left:360px;top:28px;font-size:21px}
.quote .rule{left:360px;top:67px}
.field{position:absolute;background:var(--white);border:1px solid #bdbdbd;border-radius:15px;
  font-size:8px;color:var(--text);padding:9px 0 0 16px}
.btn-submit{left:357px;top:252px;width:93px;height:31px;font-size:12.5px;font-weight:700}

.footer{position:absolute;left:0;top:1035px;width:772px;height:165px;background:var(--footer)}
.footer h2{position:absolute;left:0;right:0;top:70px;text-align:center;font-size:31px;color:var(--white)}
.footer p{position:absolute;left:0;right:0;top:131px;text-align:center;font-size:9px;color:#dddddd}
</style>
</head>
<body>

<section class="hero">
  <div class="hero-photo" role="img" aria-label="Two technicians mounting a flat-screen TV on a living room wall"></div>
  <div class="hero-fade"></div>
  <div class="logo serif">Velka Vision</div>
  <div class="phone">
    <div class="phone-icon">
      <svg width="11" height="11" viewBox="0 0 24 24"><path fill="#111" d="M6.6 10.8a15.1 15.1 0 0 0 6.6 6.6l2.2-2.2a1 1 0 0 1 1-.25 11.4 11.4 0 0 0 3.6.57 1 1 0 0 1 1 1V20a1 1 0 0 1-1 1A17 17 0 0 1 3 4a1 1 0 0 1 1-1h3.5a1 1 0 0 1 1 1c0 1.25.2 2.45.57 3.57a1 1 0 0 1-.25 1z"/></svg>
    </div>
    <span>+1 555 014 2290</span>
  </div>
  <div class="btn btn-contact">Contact Us</div>
  <h1 class="serif">Professional<br>TV Installation<br>Services</h1>
  <p class="hero-sub">Expert Technicians at Your Service</p>
  <div class="btn btn-quote">Request a Quote</div>
  <svg class="wave" style="top:395px" height="65" viewBox="0 0 772 65" preserveAspectRatio="none">
    <path d="M0 28 C150 65 300 60 450 30 C600 2 700 8 772 22 L772 65 L0 65Z" fill="var(--wave-shade)"/>
    <path d="M0 30 C150 70 300 62 450 40 C600 16 700 20 772 40 L772 65 L0 65Z" fill="var(--white)"/>
  </svg>
</section>

<section class="welcome">
  <h2 class="serif"><span>Welcome to Velka Vision</span></h2>
  <div class="rule"></div>
  <p>Sed ut perspiciatis unde omnis iste natus error sit voluptatem accusantium doloremque laudantium, totam rem aperiam, eaque ipsa quae ab illo inventore veritatis et quasi architecto beatae vitae dicta sunt explicabo. Nemo enim ipsam voluptatem quia voluptas sit aspernatur aut odit aut fugit, sed quia consequuntur magni dolores eos qui ratione voluptatem sequi nesciunt. Neque porro quisquam est, qui dolorem ipsum quia dolor sit amet, consectetur, adipisci .</p>
</section>

<section class="quote">
  <div class="quote-photo" role="img" aria-label="White ceiling-mounted projector"></div>
  <h2 class="serif">Request a Quote</h2>
  <div class="rule"></div>
  <div class="field" style="left:357px;top:91px;width:163px;height:29px">First Name</div>
  <div class="field" style="left:527px;top:91px;width:163px;height:29px">Last Name</div>
  <div class="field" style="left:357px;top:129px;width:163px;height:29px">Email id</div>
  <div class="field" style="left:527px;top:129px;width:163px;height:29px">Phone</div>
  <div class="field" style="left:357px;top:169px;width:332px;height:70px">Message</div>
  <div class="btn btn-submit">Submit</div>
</section>

<svg class="wave" style="top:1018px" height="60" viewBox="0 0 772 60" preserveAspectRatio="none">
  <rect width="772" height="60" fill="var(--footer)"/>
  <path d="M0 0 L772 0 L772 22 C650 0 520 5 380 25 C230 46 100 40 0 12Z" fill="var(--panel)"/>
  <path d="M0 12 C100 40 230 46 380 25 C520 5 650 0 772 22 L772 32 C650 12 520 16 380 36 C230 58 100 52 0 18Z" fill="var(--white)"/>
</svg>

<footer class="footer">
  <h2 class="serif">Velka Vision</h2>
  <p>Copyright © 2024 All Rights Reserved</p>
</footer>

</body>
</html>
```